VORELT B2B portal design
Fantastic design work, top communication and fast design changes! Many thanks,Jarek & Lutz from VORELT
Zielgruppe
We are a B2B Cloud Services StartUp that creates B2B logistics & supply chain processes between customer and its suppliers.
Aufgabenstellung
We need a modern responsive able design, that should consider that we are NOT presenting goods or clothes or similar on the portal pages but we show mainly data grids, kpi dashboards, forms, and setting panels to our customer and their suppliers.
The design must be clean and straight not to distract people from the important information in these data grids, kpi dashboards, forms, and settings panels.
We need our logo perfectly embedded and the pages coloured around from grey to blue.
The Designer must be able to deliver a design and transfer it to a highly responsive HTML (5) template (without technical content or further functionality). This our programmers will implement afterwards in .Net.
We need in total 3 page templates:
1. Login Page
2. Main Page with overview over the following services text (each one shown in one tile)
"ZMS (Time Frame Management)"
"DMS (Document Management)"
"REMS (Reporting Management)"
-> Note: At the end we will have up to 12 or more tiles (services) so the design should be additive
3. Data grid (e.g. list of customers)/form (e.g. customer registration form) page to show some data grid with database data
See samples for each page enclosed!!

```html
<!DOCTYPE html>
<html lang="en">
<head>
<meta charset="utf-8">
<title>VORELT – User Registration Form</title>
<link href="https://fonts.googleapis.com/css2?family=Open+Sans:wght@400;600;700&display=swap" rel="stylesheet">
<style>
  :root {
    --navy: #0d2a42;
    --chrome: #e1e6ea;
    --chrome-line: #c9d0d6;
    --page: #f7f8fa;
    --card: #ffffff;
    --text: #2f3a44;
    --muted: #5b6670;
    --placeholder: #a9b0b6;
    --field-line: #c4c9ce;
    --focus: #3f7fb5;
    --ok-bg: #e3f3d6;
    --ok-line: #86c95b;
    --ok-text: #3f8a1f;
    --err-bg: #f3ded7;
    --err-line: #d9775a;
    --err-text: #a2341a;
    --link-red: #e0362a;
  }
  * { box-sizing: border-box; margin: 0; padding: 0; }
  html, body { width: 1200px; height: 948px; overflow: hidden; }
  body { position: relative; background: var(--page); font-family: "Open Sans", sans-serif; color: var(--text); }

  .topbar { position: absolute; left: 0; top: 0; width: 1200px; height: 138px; background: var(--chrome); border-bottom: 1px solid var(--chrome-line); }
  .brand { position: absolute; left: 20px; top: 50px; display: flex; align-items: center; gap: 12px; }
  .brand-dot { width: 28px; height: 28px; border-radius: 50%; background: var(--navy); }
  .brand-name { font-size: 40px; font-weight: 700; color: var(--navy); letter-spacing: 1px; line-height: 1; }

  .user { position: absolute; right: 18px; top: 34px; display: flex; align-items: center; }
  .user-text { text-align: right; margin-right: 10px; }
  .user-name { font-size: 20px; font-weight: 600; color: var(--navy); line-height: 1.2; }
  .user-role { font-size: 14px; color: var(--muted); line-height: 1.2; }
  .avatar { width: 68px; height: 68px; border-radius: 50%; background: radial-gradient(circle at 50% 40%, #8a7a70, #3d3835); border: 2px solid #cfd5da; }
  .caret { margin-left: 8px; width: 0; height: 0; border-left: 5px solid transparent; border-right: 5px solid transparent; border-top: 6px solid #7a848c; }

  .sidebar { position: absolute; left: 0; top: 138px; width: 265px; height: 710px; background: var(--chrome); }
  .nav-item { height: 61px; display: flex; align-items: center; padding-left: 18px; gap: 11px; font-size: 20px; color: var(--navy); border-bottom: 1px solid var(--chrome-line); }
  .nav-item.active { height: 54px; background: var(--navy); color: #fff; border-bottom: none; }
  .nav-item svg { width: 28px; height: 28px; flex: none; }

  .page-title { position: absolute; left: 304px; top: 184px; font-size: 24px; font-weight: 400; color: #454d55; }
  .card { position: absolute; left: 305px; top: 240px; width: 869px; height: 604px; background: var(--card); border-bottom: 2px solid #d5dadf; }
  .card-intro { position: absolute; left: 0; top: 283px; width: 100%; }
  .intro { position: absolute; top: 44px; width: 100%; text-align: center; font-size: 17px; color: var(--text); }

  .alert { position: absolute; top: 109px; width: 365px; height: 41px; border: 1px solid; border-radius: 2px; font-size: 15px; padding-left: 14px; line-height: 39px; }
  .alert-success { left: 51px; background: var(--ok-bg); border-color: var(--ok-line); color: var(--ok-text); }
  .alert-error { left: 447px; background: var(--err-bg); border-color: var(--err-line); color: var(--err-text); }

  .field { position: absolute; width: 259px; }
  .field label { display: block; font-size: 15px; color: var(--muted); margin-bottom: 8px; }
  .field input { width: 259px; height: 42px; border: 1px solid var(--field-line); border-radius: 4px; padding: 0 14px; font-family: inherit; font-size: 15px; color: var(--text); background: #fff; }
  .field input::placeholder { color: var(--placeholder); }
  .field input.focused { border-color: var(--focus); }
  .field-user { left: 51px; top: 193px; }
  .field-pass { left: 411px; top: 193px; }
  .field-mail { left: 51px; top: 306px; }
  .field-phone { left: 411px; top: 306px; }

  .check { position: absolute; left: 52px; display: flex; align-items: center; gap: 8px; font-size: 15px; color: var(--text); }
  .check-box { width: 20px; height: 20px; border-radius: 50%; background: #dde2e6; display: flex; align-items: center; justify-content: center; }
  .check-terms { top: 405px; }
  .check-remember { top: 443px; }
  .check a { color: var(--link-red); text-decoration: none; }

  .btn-register { position: absolute; left: 57px; top: 494px; width: 119px; height: 42px; background: var(--navy); color: #fff; border: none; border-radius: 2px; font-family: inherit; font-size: 15px; font-weight: 600; letter-spacing: 0.3px; }

  .footer { position: absolute; left: 0; top: 887px; width: 1200px; height: 61px; background: #fff; border-top: 1px solid #e6e9ec; display: flex; align-items: center; justify-content: space-between; padding: 0 24px 0 14px; font-size: 17px; color: #4a535b; }
</style>
</head>
<body>
  <header class="topbar">
    <div class="brand"><span class="brand-dot"></span><span class="brand-name">VORELT</span></div>
    <div class="user">
      <div class="user-text">
        <div class="user-name">Mara Ellison</div>
        <div class="user-role">Gest User</div>
      </div>
      <div class="avatar" role="img" aria-label="User profile photo"></div>
      <span class="caret"></span>
    </div>
  </header>

  <nav class="sidebar">
    <div class="nav-item active">
      <svg viewBox="0 0 28 28" fill="none" stroke="#fff" stroke-width="2"><path d="M4 20a10 10 0 1 1 20 0z"/><path d="M14 19l5-6"/><path d="M7 15h2M14 9v2M19 11l-1 1"/></svg>Dashboard
    </div>
    <div class="nav-item">
      <svg viewBox="0 0 28 28"><circle cx="14" cy="14" r="12" fill="none" stroke="#0d2a42" stroke-width="2"/><circle cx="14" cy="11" r="4.5" fill="#0d2a42"/><path d="M6 22c2-5 14-5 16 0" fill="#0d2a42"/></svg>Profile
    </div>
    <div class="nav-item">
      <svg viewBox="0 0 28 28" fill="#0d2a42"><circle cx="10" cy="11" r="6"/><circle cx="20" cy="20" r="4.5"/><circle cx="10" cy="11" r="2" fill="#e1e6ea"/><circle cx="20" cy="20" r="1.5" fill="#e1e6ea"/></svg>Settings
    </div>
    <div class="nav-item">
      <svg viewBox="0 0 28 28" fill="#0d2a42"><rect x="3" y="14" width="3" height="10"/><rect x="9" y="10" width="3" height="14"/><rect x="15" y="12" width="3" height="12"/><rect x="21" y="8" width="3" height="16"/><path d="M3 10l7-5 6 3 8-5" fill="none" stroke="#0d2a42" stroke-width="1.6"/></svg>Charts
    </div>
    <div class="nav-item">
      <svg viewBox="0 0 28 28" fill="#0d2a42"><rect x="3" y="5" width="5" height="4"/><rect x="10" y="5" width="15" height="4"/><rect x="3" y="12" width="5" height="4"/><rect x="10" y="12" width="15" height="4"/><rect x="3" y="19" width="5" height="4"/><rect x="10" y="19" width="15" height="4"/></svg>Forms
    </div>
    <div class="nav-item">
      <svg viewBox="0 0 28 28" fill="none" stroke="#0d2a42" stroke-width="2"><circle cx="14" cy="14" r="10"/><path d="M9.5 12l4.5 4.5 4.5-4.5"/></svg>Dropdown
    </div>
    <div class="nav-item" style="border-bottom:none">
      <svg viewBox="0 0 28 28" fill="none" stroke="#0d2a42" stroke-width="2.4"><path d="M19 15v7H6V9h7"/><path d="M12 16l10-10M15 6h7v7"/></svg>Logout
    </div>
  </nav>

  <h1 class="page-title">User Registration Form</h1>

  <main class="card">
    <p class="intro">Please type your account info here.</p>
    <div class="alert alert-success">Success messae</div>
    <div class="alert alert-error">Error messae</div>

    <div class="field field-user"><label>Username:</label><input class="focused" type="text" value="John"></div>
    <div class="field field-pass"><label>Password:</label><input type="password" value="1234567"></div>
    <div class="field field-mail"><label>Mail:</label><input type="text" placeholder="Type your mail here"></div>
    <div class="field field-phone"><label>Phone:</label><input type="text" placeholder="Type your phone here"></div>

    <div class="check check-terms">
      <span class="check-box"><svg width="11" height="8" viewBox="0 0 11 8" fill="none" stroke="#6a747c" stroke-width="1.4"><path d="M1 3.5l3.5 3.5L10 1"/></svg></span>
      I Agree with <a href="#">Terms Of Use</a>
    </div>
    <div class="check check-remember">
      <span class="check-box"><svg width="11" height="8" viewBox="0 0 11 8" fill="none" stroke="#6a747c" stroke-width="1.4"><path d="M1 3.5l3.5 3.5L10 1"/></svg></span>
      Remember me
    </div>

    <button class="btn-register" type="button">REGISTER</button>
  </main>

  <footer class="footer">
    <span>© 2016 VORELT. All rights reserved.</span>
    <span>Help&nbsp; /&nbsp; Disclaimer&nbsp; /&nbsp; Contact</span>
  </footer>
</body>
</html>
```